Local fast-growing company in the service sector

We are looking for a modern business card design, which should also appear on our letterheads

Target Market(s)

Private and industrial sectors

Contact Information for Business Card

Vorname Name
Kellberger Str. 18
71398 Ostrinfeld
Tel.: 07146-839214-0
Name@agentur-kvtl.de

Colors
9d9d9d
919191
aaaaaa

Requirements
Must have
• The logo (file) in silver

```html
<!DOCTYPE html>
<html lang="de">
<head>
<meta charset="utf-8">
<title>KVTL – Visitenkarte</title>
<link rel="stylesheet" href="https://fonts.googleapis.com/css2?family=Michroma&family=Montserrat:wght@400;600&display=swap">
<style>
  :root {
    --stage: #3b3b3b;
    --card-black: #161616;
    --card-white: #f6f6f6;
    --silver: #aaaaaa;
    --silver-mid: #9d9d9d;
    --silver-dark: #919191;
    --ink: #1a1a1a;
  }
  * { margin: 0; padding: 0; box-sizing: border-box; }
  html, body { width: 799px; height: 1200px; overflow: hidden; }
  body {
    background: var(--stage);
    font-family: "Montserrat", sans-serif;
    position: relative;
  }
  .card {
    position: absolute;
    left: 90px;
    width: 620px;
    height: 376px;
    border-radius: 4px;
    overflow: hidden;
    box-shadow: 0 14px 30px rgba(0,0,0,.45);
  }
  .card--front { top: 110px; background: var(--card-black); }
  .card--back  { top: 714px; background: var(--card-white); }

  .front-mark {
    position: absolute;
    inset: 0;
    display: flex;
    align-items: center;
    justify-content: center;
    gap: 18px;
  }
  .brand-name {
    font-family: "Michroma", sans-serif;
    color: var(--silver);
    letter-spacing: 4px;
  }
  .front-mark .brand-name { font-size: 52px; }
  .brand-dot {
    width: 22px; height: 22px;
    border-radius: 50%;
    background: var(--silver-dark);
  }

  .back-shape { position: absolute; inset: 0; }
  .back-brand {
    position: absolute;
    left: 40px;
    top: 150px;
    display: flex;
    align-items: center;
    gap: 12px;
  }
  .back-brand .brand-name { font-size: 40px; }
  .back-brand .brand-dot { width: 16px; height: 16px; }

  .holder-name {
    position: absolute;
    right: 48px;
    top: 78px;
    font-family: "Michroma", sans-serif;
    font-weight: 400;
    font-size: 16px;
    letter-spacing: 1.5px;
    color: var(--ink);
    -webkit-text-stroke: .6px var(--ink);
    white-space: nowrap;
  }
  .contact {
    position: absolute;
    right: 48px;
    bottom: 40px;
    list-style: none;
    text-align: right;
    font-size: 15px;
    line-height: 22px;
    color: var(--ink);
    letter-spacing: .4px;
  }
  .contact li { display: flex; justify-content: flex-end; align-items: center; gap: 8px; }
  .contact svg { width: 14px; height: 14px; flex: none; }
</style>
</head>
<body>

  <section class="card card--front" aria-label="Visitenkarte Vorderseite">
    <div class="front-mark">
      <span class="brand-dot"></span>
      <span class="brand-name">KVTL</span>
    </div>
  </section>

  <section class="card card--back" aria-label="Visitenkarte Rückseite">
    <svg class="back-shape" viewBox="0 0 620 376" preserveAspectRatio="none" aria-hidden="true">
      <path d="M0 0 H258 C318 90 300 270 190 376 H0 Z" fill="var(--card-black)"/>
      <path d="M268 0 C332 92 314 274 204 376" fill="none" stroke="var(--card-black)" stroke-width="5"/>
    </svg>

    <div class="back-brand">
      <span class="brand-dot"></span>
      <span class="brand-name">KVTL</span>
    </div>

    <h1 class="holder-name">VORNAME NAME</h1>

    <ul class="contact">
      <li>Kellberger Str. 18</li>
      <li>71398 Ostrinfeld</li>
      <li>07146-839214-0
        <svg viewBox="0 0 16 16" aria-label="Telefon"><path fill="var(--ink)" d="M2 5c0-2 2-3 6-3s6 1 6 3v1h-3V5H5v1H2z M4 7h8l2 7H2z"/></svg>
      </li>
      <li>Name@agentur-kvtl.de
        <svg viewBox="0 0 16 16" aria-label="E-Mail"><rect x="1" y="3" width="14" height="10" fill="var(--ink)"/><path d="M1.5 3.5 8 9l6.5-5.5" fill="none" stroke="var(--card-white)" stroke-width="1.4"/></svg>
      </li>
      <li>www.agentur-kvtl.de
        <svg viewBox="0 0 16 16" aria-label="Web"><circle cx="8" cy="8" r="7" fill="var(--ink)"/><path d="M1 8h14M8 1v14M3 4.5h10M3 11.5h10" stroke="var(--card-white)" stroke-width="1"/><ellipse cx="8" cy="8" rx="3" ry="7" fill="none" stroke="var(--card-white)" stroke-width="1"/></svg>
      </li>
    </ul>
  </section>

</body>
</html>
```